Flag Order

We were just looking to order some branding flags to put on our rental equipment for our business. We would like different examples of the colors, shapes, sizes, backgrounds etc. Was thinking of just doing the plains icon instead of the whole logo on there. but open to ideas. preferably not a white background as they could get dirty,

```html
<!DOCTYPE html>
<html lang="en">
<head>
<meta charset="utf-8">
<title>Ridgeway – Flag Colour Options</title>
<link rel="stylesheet" href="https://fonts.googleapis.com/css2?family=Michroma&display=swap">
<style>
  :root {
    --board: #666666;
    --blue: #197bcf;
    --ink: #212121;
    --light: #cccccc;
    --white: #ffffff;
  }
  html, body {
    margin: 0;
    padding: 0;
    overflow: hidden;
  }
  .board {
    position: relative;
    width: 1167px;
    height: 1200px;
    background: var(--board);
    overflow: hidden;
  }
  .flag {
    position: absolute;
    width: 414px;
    height: 248px;
    display: block;
  }
  .flag--a { left: 102px; top: 132px; }
  .flag--b { left: 651px; top: 132px; }
  .flag--c { left: 102px; top: 485px; }
  .flag--d { left: 651px; top: 485px; }
  .flag--e { left: 390px; top: 819px; }

  .flag .field { fill: var(--bg); }
  .flag .band-primary { fill: var(--primary); }
  .flag .band-accent { fill: var(--accent); }
  .flag .wordmark {
    fill: var(--name);
    font-family: "Michroma", sans-serif;
    font-size: 44px;
  }

  .theme-grey  { --bg: var(--light); --primary: var(--ink);   --accent: var(--blue);  --name: var(--ink); }
  .theme-blue  { --bg: var(--blue);  --primary: var(--ink);   --accent: var(--white); --name: var(--ink); }
  .theme-dark  { --bg: var(--ink);   --primary: var(--white); --accent: var(--blue);  --name: var(--white); }
  .theme-mono  { --bg: var(--blue);  --primary: var(--ink);   --accent: var(--ink);   --name: var(--ink); }
  .theme-white { --bg: var(--blue);  --primary: var(--white); --accent: var(--white); --name: var(--white); }
</style>
</head>
<body>
<main class="board">

  <svg class="flag flag--a theme-grey" viewBox="0 0 676 405" aria-label="Grey flag option">
    <rect class="field" width="676" height="405"/>
    <polygon class="band-primary" points="536,0 598,0 536,152 476,152"/>
    <polygon class="band-accent" points="630,0 690,0 648,103 588,103"/>
    <polygon class="band-primary" points="80,240 140,240 52,405 -8,405"/>
    <polygon class="band-accent" points="162,240 222,240 148,383 90,383"/>
    <rect class="band-accent" x="196" y="172" width="34" height="34"/>
    <text class="wordmark" x="262" y="206" textLength="263" lengthAdjust="spacingAndGlyphs">RIDGEWAY</text>
  </svg>

  <svg class="flag flag--b theme-blue" viewBox="0 0 676 405" aria-label="Blue flag option with black and white bands">
    <rect class="field" width="676" height="405"/>
    <polygon class="band-primary" points="536,0 598,0 536,152 476,152"/>
    <polygon class="band-accent" points="630,0 690,0 648,103 588,103"/>
    <polygon class="band-primary" points="80,240 140,240 52,405 -8,405"/>
    <polygon class="band-accent" points="162,240 222,240 148,383 90,383"/>
    <rect class="band-accent" x="196" y="172" width="34" height="34"/>
    <text class="wordmark" x="262" y="206" textLength="263" lengthAdjust="spacingAndGlyphs">RIDGEWAY</text>
  </svg>

  <svg class="flag flag--c theme-dark" viewBox="0 0 676 405" aria-label="Black flag option">
    <rect class="field" width="676" height="405"/>
    <polygon class="band-primary" points="536,0 598,0 536,152 476,152"/>
    <polygon class="band-accent" points="630,0 690,0 648,103 588,103"/>
    <polygon class="band-primary" points="80,240 140,240 52,405 -8,405"/>
    <polygon class="band-accent" points="162,240 222,240 148,383 90,383"/>
    <rect class="band-accent" x="196" y="172" width="34" height="34"/>
    <text class="wordmark" x="262" y="206" textLength="263" lengthAdjust="spacingAndGlyphs">RIDGEWAY</text>
  </svg>

  <svg class="flag flag--d theme-mono" viewBox="0 0 676 405" aria-label="Blue flag option with black bands">
    <rect class="field" width="676" height="405"/>
    <polygon class="band-primary" points="536,0 598,0 536,152 476,152"/>
    <polygon class="band-accent" points="630,0 690,0 648,103 588,103"/>
    <polygon class="band-primary" points="80,240 140,240 52,405 -8,405"/>
    <polygon class="band-accent" points="162,240 222,240 148,383 90,383"/>
    <rect class="band-accent" x="196" y="172" width="34" height="34"/>
    <text class="wordmark" x="262" y="206" textLength="263" lengthAdjust="spacingAndGlyphs">RIDGEWAY</text>
  </svg>

  <svg class="flag flag--e theme-white" viewBox="0 0 676 405" aria-label="Blue flag option with white bands">
    <rect class="field" width="676" height="405"/>
    <polygon class="band-primary" points="536,0 598,0 536,152 476,152"/>
    <polygon class="band-accent" points="630,0 690,0 648,103 588,103"/>
    <polygon class="band-primary" points="80,240 140,240 52,405 -8,405"/>
    <polygon class="band-accent" points="162,240 222,240 148,383 90,383"/>
    <rect class="band-accent" x="196" y="172" width="34" height="34"/>
    <text class="wordmark" x="262" y="206" textLength="263" lengthAdjust="spacingAndGlyphs">RIDGEWAY</text>
  </svg>

</main>
</body>
</html>
```